Business Card - high end, modern health care

Hey designers!

We need a double sided business card for the boutique, cutting edge physical therapy rehabilitation centre in Sydney's Northern Beaches.

With the most qualified physios in the area The Harbourview Motion Clinic does what other physiotherapy practices do not, we take our time with our patients giving them longer appointments, better physios and therefor faster results!

We guarantee that the service people receive at THMC will be unparalleled.

Hence we need a business card to reflect our modern, boutique, high end service. The final design needs to reflect that we are in a class of our own yet with the feel of beachside retreat.

Below I have attached our logo in both blue on white and white on blue. The exact colour is;
and the font that we have used in our logo is Tex Gyre Aventador.

I like the idea of the blue as the main colour as it is more eye catching and our signage onto the main road will be in this blue and in the interest of consistency across marketing the blue needs to be a part of the design. However I would appreciate a few designs onto a wooden background as this is a visual theme within the fitout of the practice.

The design needs to be of standard size (91x55mm).

Target Market(s)

We target people who have an end outcome in mind and those who have had poor experiences with other providers and ensure that everyone gets the care that they deserve with a premium service that is tailored to the individuals circumstances. As a premium service, the target market is highly educated, business and tech savvy with the additional target market of elderly people who have self funded their retirement and see value in paying for the best ongoing rehabilitation to maintain independence.

Industry/Entity Type

Physical Therapy

Contact Information for Business Card

Name, designation( Titled Musculoskeletal Physiotherapist... there will also be those in the company that have multiple designations ie 5 or 6 words long), phone number, email, facebook, instagram, address

Font styles to use
Sans Serif

Colors

Designer to choose colors to be used in the design.

Requirements
Must have
• Front - The logo as large as possible, blue or wooden theme, and all of the important details.
• Back - A blank space/lines on which to write appointment times (no "Appointment, date, time" etc.)
Nice to have
• facebook url
• logos for facebook and instagram
• Mini logos for the phone and email?

```html
<!DOCTYPE html>
<html lang="en">
<head>
<meta charset="UTF-8">
<title>The Harbourview Motion Clinic – Business Card</title>
<link href="https://fonts.googleapis.com/css2?family=Raleway:wght@400;500;700&display=swap" rel="stylesheet">
<style>
  :root {
    --brand-blue: #0f59a8;
    --ink: #1d1d1f;
    --muted-ink: #333;
    --rule: #8a8a8a;
    --paper: #ffffff;
    --backdrop: #3f3d68;
    --social-a: #1f8fd6;
    --social-b: #e9559a;
  }
  * { margin: 0; padding: 0; box-sizing: border-box; }
  html, body { width: 1200px; height: 1200px; overflow: hidden; }
  body {
    background: var(--backdrop);
    font-family: "Raleway", sans-serif;
    position: relative;
  }
  .card {
    position: absolute;
    left: 240px;
    width: 720px;
    height: 418px;
    background: var(--paper);
    border-radius: 34px;
    overflow: hidden;
  }
  .card--front { top: 142px; }
  .card--back { top: 638px; }

  .front-band { position: absolute; inset: 0; }

  .brand-large {
    position: absolute;
    left: 40px; top: 92px;
    width: 240px;
    text-align: center;
    color: var(--brand-blue);
    font-weight: 700;
  }
  .brand-large__circle {
    width: 110px; height: 110px;
    border-radius: 50%;
    background: var(--brand-blue);
    margin: 0 auto 20px;
  }
  .brand-large__name { font-size: 22px; line-height: 1.2; letter-spacing: 0.04em; }

  .brand-inline {
    position: absolute;
    left: 344px; top: 184px;
    display: flex; align-items: center; gap: 12px;
    color: var(--paper);
    font-weight: 700;
  }
  .brand-inline__circle {
    width: 48px; height: 48px; border-radius: 50%;
    background: var(--paper); flex: none;
  }
  .brand-inline__name { font-size: 21px; line-height: 1.1; letter-spacing: 0.05em; }

  .back-divider {
    position: absolute; left: 138px; top: 0; bottom: 0;
    width: 2px; background: var(--rule);
  }
  .brand-vertical {
    position: absolute;
    left: 69px; top: 240px;
    transform: translate(-50%, -50%) rotate(-90deg);
    display: flex; align-items: center; gap: 12px;
    white-space: nowrap;
    color: var(--brand-blue);
    font-weight: 700;
  }
  .brand-vertical__circle { width: 36px; height: 36px; border-radius: 50%; background: var(--brand-blue); }
  .brand-vertical__name { font-size: 19px; line-height: 1.1; letter-spacing: 0.04em; }

  .person { position: absolute; left: 166px; top: 78px; }
  .person__name { font-size: 27px; font-weight: 500; color: var(--ink); }
  .person__name span { color: var(--brand-blue); }
  .person__title { font-size: 17px; font-weight: 500; color: var(--muted-ink); margin-top: 10px; }

  .rule {
    position: absolute; left: 138px; width: 524px;
    height: 2px; background: var(--rule);
  }
  .rule--top { top: 159px; }
  .rule--bottom { top: 321px; }
  .write-line {
    position: absolute; left: 171px; width: 491px; top: 378px;
    border-top: 1.5px dashed var(--rule);
  }

  .contact {
    position: absolute; left: 166px;
    display: flex; align-items: center; gap: 16px;
    font-size: 20px; color: var(--ink);
  }
  .contact--phone { top: 190px; }
  .contact--email { top: 226px; }
  .contact svg { width: 26px; height: 26px; flex: none; }

  .social {
    position: absolute; top: 280px;
    display: flex; align-items: center; gap: 11px;
    font-size: 17px; color: var(--muted-ink);
  }
  .social--page { left: 166px; }
  .social--gallery { left: 413px; }
  .social__dot { width: 24px; height: 24px; border-radius: 50%; }
  .social--page .social__dot { background: var(--social-a); }
  .social--gallery .social__dot { background: var(--social-b); }
</style>
</head>
<body>

<section class="card card--front">
  <svg class="front-band" viewBox="0 0 720 418" width="720" height="418" aria-hidden="true">
    <path d="M380 0 Q250 211 352 418 L720 418 L720 0 Z" fill="var(--brand-blue)"/>
  </svg>
  <div class="brand-large">
    <div class="brand-large__circle"></div>
    <div class="brand-large__name">THE HARBOURVIEW<br>MOTION CLINIC</div>
  </div>
  <div class="brand-inline">
    <div class="brand-inline__circle"></div>
    <div class="brand-inline__name">THE HARBOURVIEW<br>MOTION CLINIC</div>
  </div>
</section>

<section class="card card--back">
  <div class="back-divider"></div>
  <div class="brand-vertical">
    <div class="brand-vertical__circle"></div>
    <div class="brand-vertical__name">THE HARBOURVIEW<br>MOTION CLINIC</div>
  </div>

  <div class="person">
    <div class="person__name">Name of <span>Person</span></div>
    <div class="person__title">Designation</div>
  </div>
  <div class="rule rule--top"></div>

  <div class="contact contact--phone">
    <svg viewBox="0 0 26 26" aria-hidden="true">
      <circle cx="13" cy="13" r="11.5" fill="none" stroke="#111" stroke-width="2"/>
      <path d="M9 7.5c-1 .6-1.4 1.8-1 3 1 3 3.5 5.6 6.5 6.6 1.2.4 2.4 0 3-1l-2.2-2.2-1.6 1c-1.6-.8-2.9-2.1-3.6-3.6l1-1.6Z" fill="#111"/>
    </svg>
    <span>555.010.4186</span>
  </div>
  <div class="contact contact--email">
    <svg viewBox="0 0 26 26" aria-hidden="true">
      <rect x="2" y="6" width="22" height="14" fill="#111"/>
      <path d="M3 7l10 8 10-8" fill="none" stroke="#fff" stroke-width="1.6"/>
    </svg>
    <span>companyname@email.com</span>
  </div>

  <div class="social social--page">
    <div class="social__dot"></div><span>socialpage/name</span>
  </div>
  <div class="social social--gallery">
    <div class="social__dot"></div><span>gallery_name</span>
  </div>
  <div class="rule rule--bottom"></div>
  <div class="write-line"></div>
</section>

</body>
</html>
```